Need help in designing new business card utilizing our new logo.

BuildMark Solutions works with Construction Business Owners, Managers & IT Professionals to strengthen software usage and increase user productivity.

Our Construction Accounting and Mobile Field Management Software Clients engage with us in the following areas:

New Software Implementations
Software Re-Implementations
Redesigning Software Usage at the User Level
Project Coordination & Management
Continued Software Support

Old tag line:
Weighing Options - Implementing Solutions

www.buildmark-solutions.example

Ridge 4 is a product, but not needed for a new business card.

```html
<!DOCTYPE html>
<html lang="en">
<head>
<meta charset="utf-8">
<title>BuildMark Solutions – Business Card</title>
<link rel="stylesheet" href="https://fonts.googleapis.com/css2?family=Open+Sans:wght@400;600&family=Roboto+Condensed:wght@400&display=swap">
<style>
  :root {
    --backdrop: #8b8b8b;
    --brand-blue: #0c17a4;
    --paper: #ffffff;
    --ink: #3a3a3a;
    --rule: #b5b5b5;
  }
  html, body {
    margin: 0;
    padding: 0;
    width: 1200px;
    height: 1200px;
    overflow: hidden;
    background: var(--backdrop);
    font-family: "Open Sans", sans-serif;
  }
  .canvas { position: relative; width: 1200px; height: 1200px; }

  .card {
    position: absolute;
    top: 310px;
    height: 595px;
    box-shadow: 2px 3px 6px rgba(0,0,0,0.45);
    overflow: hidden;
  }
  .card-front { left: 234px; width: 364px; background: var(--paper); }
  .card-back { left: 627px; width: 370px; background: var(--brand-blue); }

  /* Front */
  .brand {
    position: absolute;
    top: 102px;
    left: 0;
    width: 364px;
    display: flex;
    align-items: center;
    justify-content: center;
    gap: 14px;
  }
  .brand-square { width: 44px; height: 44px; background: var(--brand-blue); }
  .brand-name {
    color: var(--brand-blue);
    font-weight: 600;
    font-size: 27px;
    line-height: 1.1;
    letter-spacing: 0.5px;
  }
  .brand-name span { display: block; }

  .specialty {
    position: absolute;
    top: 199px;
    width: 364px;
    text-align: center;
    font-family: "Roboto Condensed", sans-serif;
    font-size: 19.5px;
    color: var(--ink);
    letter-spacing: -0.3px;
  }

  .person { position: absolute; top: 285px; width: 364px; text-align: center; }
  .person-name { color: var(--brand-blue); font-size: 22px; line-height: 28px; }
  .person-role { color: var(--ink); font-size: 17.5px; line-height: 22px; }

  .rule {
    position: absolute;
    left: 79px;
    width: 206px;
    height: 1px;
    background: var(--rule);
  }
  .rule-top { top: 339px; }
  .rule-bottom { top: 450px; }

  .contact {
    position: absolute;
    top: 350px;
    width: 364px;
    text-align: center;
    font-size: 17px;
    line-height: 21.5px;
    color: var(--ink);
  }
  .contact b { color: var(--brand-blue); font-weight: 600; }
  .contact .web { color: var(--brand-blue); font-weight: 600; }

  .address {
    position: absolute;
    top: 456px;
    width: 364px;
    text-align: center;
    font-size: 17px;
    line-height: 21.5px;
    color: var(--ink);
  }

  .tagline-band {
    position: absolute;
    left: 0;
    bottom: 0;
    width: 364px;
    height: 77px;
    background: var(--brand-blue);
    color: var(--paper);
    font-weight: 600;
    font-size: 15px;
    line-height: 19px;
    text-align: center;
    display: flex;
    flex-direction: column;
    justify-content: center;
  }

  /* Back */
  .service {
    position: absolute;
    left: 0;
    width: 370px;
    text-align: center;
  }
  .service svg { display: block; margin: 0 auto; }
  .service-label {
    margin-top: 12px;
    color: var(--paper);
    font-size: 13.5px;
    letter-spacing: -0.2px;
    text-transform: uppercase;
  }
</style>
</head>
<body>
<main class="canvas">

  <section class="card card-front">
    <div class="brand">
      <div class="brand-square"></div>
      <div class="brand-name"><span>BUILDMARK</span><span>SOLUTIONS</span></div>
    </div>
    <p class="specialty" style="margin:0">Construction Accounting Software Consultants</p>

    <div class="person">
      <div class="person-name">DANIEL HARPER</div>
      <div class="person-role">Managing Director</div>
    </div>
    <div class="rule rule-top"></div>

    <div class="contact">
      <div><b>P:</b> 044-555 010 200</div>
      <div><b>M:</b> 044-555 010 200</div>
      <div><b>E:</b> info@buildmark-solutions.example</div>
      <div class="web">www.buildmark-solutions.example</div>
    </div>
    <div class="rule rule-bottom"></div>

    <div class="address">
      <div>48 Foundry Lane</div>
      <div>Eastvale, 204810.</div>
    </div>

    <div class="tagline-band">
      <span>WEIGHING OPTIONS</span>
      <span>IMPLEMENTING SOLUTIONS</span>
    </div>
  </section>

  <section class="card card-back">
    <div class="service" style="top:18px">
      <svg width="68" height="76" viewBox="0 0 68 76" role="img" aria-label="Icon: person connected to a network"><polygon points="34,0 68,19 68,57 34,76 0,57 0,19" fill="#fff"/></svg>
      <div class="service-label">Project Coordination Management</div>
    </div>
    <div class="service" style="top:130px">
      <svg width="68" height="76" viewBox="0 0 68 76" role="img" aria-label="Icon: new software box with disc"><polygon points="34,0 68,19 68,57 34,76 0,57 0,19" fill="#fff"/></svg>
      <div class="service-label">New Software Implementations</div>
    </div>
    <div class="service" style="top:241px">
      <svg width="68" height="76" viewBox="0 0 68 76" role="img" aria-label="Icon: disc with circular arrows"><polygon points="34,0 68,19 68,57 34,76 0,57 0,19" fill="#fff"/></svg>
      <div class="service-label">Redesigning Software Usage at the User Level</div>
    </div>
    <div class="service" style="top:352px">
      <svg width="68" height="76" viewBox="0 0 68 76" role="img" aria-label="Icon: software box with refresh arrow"><polygon points="34,0 68,19 68,57 34,76 0,57 0,19" fill="#fff"/></svg>
      <div class="service-label">Software Re-Implementations</div>
    </div>
    <div class="service" style="top:464px">
      <svg width="68" height="76" viewBox="0 0 68 76" role="img" aria-label="Icon: support agent with headset"><polygon points="34,0 68,19 68,57 34,76 0,57 0,19" fill="#fff"/></svg>
      <div class="service-label">Continued Software Support</div>
    </div>
  </section>

</main>
</body>
</html>
```